Marlow Estate Fixers (Handyman / Home Improvement Company)

Looking for a double sided professional looking business card with Logo attached to be highlighted on one side and throwing in an image of a handyman as an option would be nice to see as well. We are a company focused on providing quality Handyman and Home improvement services in a timely manner that is done right the first time with integrity

Industry/Entity Type

Handyman / Home Improvement

Contact Information for Business Card

(LOGO, Name, Mobile and office phone numbers, email) on front side of card, (the words "The SOLUTION to all of your Handyman and Home Improvement needs" followed by "Family Owned and Operated" at the very bottom) on the back.

Colors
EB3D1F
EC4F4E
F09395
F8D3D4
FCEDEE

Requirements
Must have
• Red, Gray, Black Color scheme
Should not have
• No Yellow or Blue colors

```html
<!DOCTYPE html>
<html lang="en">
<head>
<meta charset="utf-8">
<title>Marlow Estate Fixers – Business Card</title>
<link rel="stylesheet" href="https://fonts.googleapis.com/css2?family=Montserrat:wght@400;600;700&family=Anton&display=swap">
<style>
  :root {
    --backdrop: #1f1f1f;
    --red: #e8262c;
    --ink: #333333;
    --rule: #3a3a3a;
    --silver-dark: #9d9d9d;
    --silver-mid: #c9c9c9;
    --silver-light: #ffffff;
    --art-dark: #7a7a80;
    --art-light: #d9d9dc;
  }
  * { box-sizing: border-box; margin: 0; padding: 0; }
  html, body { width: 1200px; height: 1059px; overflow: hidden; }
  body {
    background: var(--backdrop);
    font-family: "Montserrat", Arial, sans-serif;
    position: relative;
  }
  .card {
    position: absolute;
    left: 262px;
    border-radius: 24px;
    overflow: hidden;
    background: linear-gradient(180deg,
      var(--silver-dark) 0%,
      var(--silver-mid) 25%,
      var(--silver-light) 53%,
      var(--silver-mid) 80%,
      var(--silver-dark) 100%);
    box-shadow: -6px 6px 14px rgba(0,0,0,0.45);
  }
  .card--front { top: 95px; width: 714px; height: 408px; }
  .card--back { top: 529px; width: 717px; height: 410px; }

  /* Front */
  .brand {
    position: absolute;
    left: 430px; top: 150px;
    width: 250px;
    display: flex; align-items: center; gap: 10px;
  }
  .brand__mark { width: 22px; height: 22px; background: var(--red); flex: none; }
  .brand__name {
    font-weight: 700; font-size: 25px; line-height: 1.1;
    color: var(--red); text-transform: uppercase;
  }
  .person__name {
    position: absolute; left: 35px; top: 250px;
    font-weight: 600; font-size: 28px; color: var(--red);
  }
  .person__role {
    position: absolute; left: 35px; top: 295px;
    font-weight: 400; font-size: 19px; color: var(--ink);
  }
  .rule {
    position: absolute; left: 36px; top: 335px;
    width: 648px; height: 2px; background: var(--rule);
  }
  .contacts {
    position: absolute; left: 36px; top: 350px;
    display: flex; align-items: center; gap: 20px;
    font-size: 19px; color: var(--ink); white-space: nowrap;
  }
  .contact { display: flex; align-items: center; gap: 10px; }
  .contact svg { flex: none; fill: var(--red); }

  /* Back */
  .tagline {
    position: absolute; left: 20px; top: 92px; width: 400px;
    text-align: center;
  }
  .tagline__lead {
    font-weight: 700; font-size: 30px; color: var(--ink);
    white-space: nowrap; line-height: 40px;
  }
  .tagline__focus {
    font-family: "Anton", Impact, sans-serif;
    font-size: 43px; line-height: 56px; color: var(--red);
    transform: scaleY(1.08);
  }
  .tagline__small { font-size: 36px; }
  .family {
    position: absolute; left: 20px; top: 356px; width: 400px;
    text-align: center; font-weight: 700; font-size: 23px; color: var(--ink);
  }
  .handyman-art {
    position: absolute; left: 430px; top: 18px;
    width: 270px; height: 382px; border-radius: 16px;
    background: linear-gradient(180deg, var(--art-light), var(--art-dark));
  }
</style>
</head>
<body>
  <section class="card card--front">
    <div class="brand">
      <span class="brand__mark"></span>
      <span class="brand__name">Marlow Estate Fixers</span>
    </div>
    <div class="person__name">Daniel Harper</div>
    <div class="person__role">Owner</div>
    <div class="rule"></div>
    <div class="contacts">
      <div class="contact">
        <svg width="14" height="22" viewBox="0 0 14 22" aria-hidden="true"><path d="M2 0h10a2 2 0 0 1 2 2v18a2 2 0 0 1-2 2H2a2 2 0 0 1-2-2V2a2 2 0 0 1 2-2zm0 3v14h10V3zm5 15.5a1.3 1.3 0 1 0 0 2.6 1.3 1.3 0 0 0 0-2.6z"/></svg>
        <span>044-987 654 321</span>
      </div>
      <div class="contact">
        <svg width="20" height="16" viewBox="0 0 20 16" aria-hidden="true"><path d="M0 5c0-3 4-5 10-5s10 2 10 5v1h-5V4H5v2H0zm4 3h12l3 8H1z"/></svg>
        <span>044-987 654 321</span>
      </div>
      <div class="contact">
        <svg width="19" height="14" viewBox="0 0 19 14" aria-hidden="true"><path d="M0 0h19v2L9.5 8 0 2zm0 4l9.5 6L19 4v10H0z"/></svg>
        <span>hello@marlowfixers.com</span>
      </div>
    </div>
  </section>

  <section class="card card--back">
    <div class="tagline">
      <div class="tagline__lead">Your SOLUTION to all of</div>
      <div class="tagline__focus"><span class="tagline__small">your</span> Handyman <span class="tagline__small">and</span></div>
      <div class="tagline__focus">Home Improvement</div>
      <div class="tagline__focus">Needs</div>
    </div>
    <div class="family">Family Owned and Operated</div>
    <div class="handyman-art" role="img" aria-label="Cartoon handyman in work overalls holding a pipe wrench and spanner"></div>
  </section>
</body>
</html>
```